BrimFalcon Business Cards

We have a defined brand. Please visit our website to get a feel for the product and the color pallets. www.brimfalcon-example.com

We need an updated, world class business card design. (See the attached existing card design). Please utilize BOTH sides of the card as shown and be creative with the layout. I do want the horse head icon to be positioned as it is with the existing card.

The remainder of the layout can be customized and I also want it vertically oriented.

Attached are the logo files and please use the colors as follows:
Green - #A5CE39
Tan - #CDBD99
Black

Feel free to play with the colors.

```html
<!DOCTYPE html>
<html lang="en">
<head>
<meta charset="utf-8">
<title>BrimFalcon Business Cards</title>
<link href="https://fonts.googleapis.com/css2?family=Open+Sans:wght@400;600;700&family=Montserrat:wght@600&display=swap" rel="stylesheet">
<style>
  :root {
    --backdrop: #2a2a2a;
    --card: #ffffff;
    --ink: #111111;
    --ink-soft: #2b2b2b;
    --lime: #a5ce39;
    --rule: #3a8f3a;
    --edge: #1f3fa0;
    --ghost-a: #e6e6e6;
    --ghost-b: #f7f7f7;
  }
  * { margin: 0; padding: 0; box-sizing: border-box; }
  html, body { width: 1200px; height: 900px; overflow: hidden; }
  body {
    background: var(--backdrop);
    font-family: "Open Sans", sans-serif;
    color: var(--ink);
    position: relative;
  }
  .card {
    position: absolute;
    top: 135px;
    width: 360px;
    height: 630px;
    background: var(--card);
    border-radius: 26px;
    overflow: hidden;
  }
  .card--front { left: 200px; border-bottom: 4px solid var(--edge); }
  .card--back { left: 640px; }

  .brand { display: flex; align-items: center; gap: 12px; white-space: nowrap; }
  .brand__mark {
    width: 40px; height: 40px; border-radius: 50%;
    background: var(--ink);
    flex: none;
  }
  .brand__name {
    font-weight: 700;
    font-size: 30px;
    line-height: 1;
    color: var(--ink);
  }
  .brand__tagline {
    font-weight: 600;
    font-size: 13px;
    letter-spacing: 3px;
    margin-top: 8px;
    margin-left: 52px;
    white-space: nowrap;
    color: var(--ink);
  }

  .card--front .lockup {
    position: absolute;
    left: 50%; top: 50%;
    transform: translate(-50%, -50%);
  }

  .card--back .lockup { position: absolute; left: 32px; top: 48px; }
  .card--back .brand__name { font-size: 27px; }
  .card--back .brand__mark { width: 36px; height: 36px; }
  .card--back .brand__tagline { font-size: 12px; letter-spacing: 2.6px; margin-left: 48px; }

  .ghost {
    position: absolute;
    right: -90px; bottom: -70px;
    width: 320px; height: 360px;
    border-radius: 50%;
    background: radial-gradient(circle at 45% 45%, var(--ghost-a), var(--ghost-b) 70%, transparent 72%);
  }

  .rule { position: absolute; height: 2px; background: var(--rule); }
  .rule--long { left: 32px; top: 180px; width: 296px; }
  .rule--short { left: 32px; top: 282px; width: 170px; }

  .person { position: absolute; left: 32px; top: 210px; }
  .person__name {
    font-family: "Montserrat", sans-serif;
    font-weight: 600;
    font-size: 22px;
    letter-spacing: 5px;
    color: var(--ink-soft);
    white-space: nowrap;
  }
  .person__role { font-size: 13px; color: var(--ink-soft); margin-top: 4px; }

  .contacts { position: absolute; left: 32px; top: 306px; list-style: none; }
  .contacts li {
    display: flex; align-items: center; gap: 12px;
    font-size: 14px; color: var(--ink-soft);
    height: 36px;
    white-space: nowrap;
  }
  .icon {
    width: 26px; height: 26px; border-radius: 50%;
    background: var(--lime);
    display: flex; align-items: center; justify-content: center;
    flex: none;
  }
  .icon svg { width: 14px; height: 14px; }

  .address {
    position: absolute; left: 32px; top: 440px;
    display: flex; align-items: flex-start; gap: 12px;
    font-size: 14px; line-height: 1.5; color: var(--ink);
  }
</style>
</head>
<body>

<section class="card card--front">
  <div class="lockup">
    <div class="brand">
      <span class="brand__mark"></span>
      <span class="brand__name">BrimFalcon Labs</span>
    </div>
    <div class="brand__tagline">Performance Driven EVs</div>
  </div>
</section>

<section class="card card--back">
  <div class="ghost" role="img" aria-label="Faint large brand emblem decoration"></div>

  <div class="lockup">
    <div class="brand">
      <span class="brand__mark"></span>
      <span class="brand__name">BrimFalcon Labs</span>
    </div>
    <div class="brand__tagline">Performance Driven EVs</div>
  </div>

  <div class="rule rule--long"></div>

  <div class="person">
    <div class="person__name">JORDAN REYES</div>
    <div class="person__role">CEO/Managing Director</div>
  </div>

  <div class="rule rule--short"></div>

  <ul class="contacts">
    <li>
      <span class="icon"><svg viewBox="0 0 16 16"><path d="M4 1l3 3-1.5 2a8 8 0 0 0 4.5 4.5L12 9l3 3-2 2.5C7 14 2 9 1.5 3z" fill="#fff"/></svg></span>
      555-014-2288
    </li>
    <li>
      <span class="icon"><svg viewBox="0 0 16 16"><rect x="1.5" y="3.5" width="13" height="9" fill="none" stroke="#fff" stroke-width="1.5"/><path d="M1.5 3.5l6.5 5 6.5-5" fill="none" stroke="#fff" stroke-width="1.5"/></svg></span>
      jreyes@brimfalcon-example.com
    </li>
    <li>
      <span class="icon"><svg viewBox="0 0 16 16" fill="none" stroke="#fff" stroke-width="1.3"><circle cx="8" cy="8" r="6.5"/><ellipse cx="8" cy="8" rx="3" ry="6.5"/><path d="M1.5 8h13M2.5 4.5h11M2.5 11.5h11"/></svg></span>
      www.brimfalcon-example.com
    </li>
  </ul>

  <div class="address">
    <span class="icon"><svg viewBox="0 0 16 16"><path d="M8 1a5 5 0 0 0-5 5c0 4 5 9 5 9s5-5 5-9a5 5 0 0 0-5-5z" fill="#fff"/><circle cx="8" cy="6" r="2" fill="#a5ce39"/></svg></span>
    <span>410 Harbor Lane NW<br>Suite 200, Lakeview MI 40012</span>
  </div>
</section>

</body>
</html>
```